I have a website called Okenta Holdings (okentaholdings.com) that I would like to have redesigned. Most of the content is already created, but I need a new design. You can also see my other website at brambleacres.com. I am open to a new logo or modifying the current logo if you have a good idea. Please feel free to use other images for the home page (and maybe some other locations) if you feel they provide a better look and feel to the website. I prefer a modern look.

Important: You do not have to use the images I've provided for the home page. Feel free to find your own stock photos. You don't have to pay for them unless I select your design.

1) Please use wix.com to make your changes so that I can edit it later.
2) I will need all the graphics files to be saved so I can dowload it for later.
3) I will be adding more content to the site later.
4) This site will likely be transferred over to brambleacres.com so if you make a logo please make one for Okenta Holdings and one for Bramble Acres.
5) You can use other images that you feel would help the look and feel of the website.

```html
<!DOCTYPE html>
<html lang="en">
<head>
<meta charset="utf-8">
<title>Bramble Acres</title>
<link rel="stylesheet" href="https://fonts.googleapis.com/css2?family=Poppins:wght@400;500;600;700&display=swap">
<style>
:root{
  --navy:#0b2d5e;
  --brand:#1b6fc4;
  --ink:#111111;
  --text:#333333;
  --muted:#555555;
  --light:#f6f6f6;
  --line:#c9c9c9;
  --white:#ffffff;
}
*{margin:0;padding:0;box-sizing:border-box}
html,body{width:1200px;height:4781px;overflow:hidden}
body{position:relative;background:var(--white);font-family:'Poppins',sans-serif;color:var(--text)}
.abs{position:absolute}
/* header */
.site-header{position:absolute;left:0;top:0;width:1200px;height:76px;background:var(--white);border-top:3px solid var(--navy)}
.brand{position:absolute;left:100px;top:20px;display:flex;align-items:center;gap:12px}
.brand-square{width:30px;height:30px;background:var(--navy)}
.brand-name{font-size:27px;font-weight:600;color:var(--brand)}
.nav a{position:absolute;top:30px;font-size:14px;font-weight:500;color:var(--ink);text-decoration:none;letter-spacing:.3px}
/* hero */
.hero{position:absolute;left:0;top:76px;width:1200px;height:625px;
  background:linear-gradient(180deg,#8a7fa6 0%,#e2a06a 28%,#c07848 45%,#6c6f78 62%,#3f5a44 85%,#2f4a30 100%)}
.hero-title{position:absolute;left:100px;top:262px;font-size:45px;line-height:52px;font-weight:700;color:var(--white);text-transform:uppercase}
.hero-text{position:absolute;left:100px;top:376px;width:440px;font-size:16px;line-height:30px;color:var(--white)}
.btn{position:absolute;display:flex;align-items:center;justify-content:center;background:var(--navy);color:var(--white);font-size:13px;font-weight:600;letter-spacing:.4px;text-transform:uppercase}
/* section titles */
.section-title{position:absolute;left:0;width:1200px;text-align:center;font-size:39px;line-height:48px;color:var(--ink);text-transform:uppercase;font-weight:400}
.section-title b{font-weight:700}
.title-rule{position:absolute;left:553px;width:94px;height:4px;background:var(--navy)}
/* services */
.service-card{position:absolute;top:863px;width:316px;height:406px;background:var(--light)}
.service-photo{width:316px;height:211px}
.service-card h3{position:absolute;left:17px;top:232px;font-size:22px;font-weight:600;color:var(--ink)}
.service-card p{position:absolute;left:17px;top:270px;width:290px;font-size:13.5px;line-height:26px;color:var(--text)}
.text-link{position:absolute;left:17px;top:358px;font-size:12.5px;font-weight:600;color:var(--navy);text-decoration:underline;text-transform:uppercase}
/* about */
.about-panel{position:absolute;left:0;top:1362px;width:600px;height:530px;background:var(--light)}
.about-photo{position:absolute;left:600px;top:1362px;width:600px;height:530px;background:linear-gradient(160deg,#9aa9b8 0%,#6f8294 40%,#3d4f66 70%,#5e6b58 100%)}
.about-title{position:absolute;left:100px;top:1443px;font-size:40px;line-height:48px;color:var(--ink);text-transform:uppercase}
.about-text{position:absolute;left:100px;top:1526px;width:450px;font-size:15px;line-height:30.2px;color:var(--text)}
/* stats */
.stats{position:absolute;left:0;top:1892px;width:1200px;height:188px;background:var(--navy)}
.stat{position:absolute;top:56px;width:240px;text-align:center;color:var(--white)}
.stat strong{display:block;font-size:37px;line-height:44px;font-weight:600}
.stat span{display:block;font-size:17px;line-height:24px}
.stat-divider{position:absolute;top:60px;width:1px;height:70px;background:rgba(255,255,255,.55)}
/* projects */
.project{position:absolute;width:321px;height:321px}
.project-overlay{position:absolute;left:14px;top:14px;width:293px;height:293px;background:rgba(11,45,94,.82);color:var(--white);text-align:center}
.project-overlay h4{margin-top:104px;font-size:20px;font-weight:500}
.project-overlay p{margin:6px 22px 0;font-size:13px;line-height:25px}
/* clients */
.clients{position:absolute;left:0;top:3014px;width:1200px;height:299px;background:var(--light)}
.client-strip{position:absolute;left:163px;top:143px;width:876px;height:104px;background:#fafafa}
.client{position:absolute;top:180px;width:160px;text-align:center;font-size:25px;font-weight:500;color:#4a4a4a}
/* contact */
.map{position:absolute;left:100px;top:3493px;width:1000px;height:436px;background:linear-gradient(135deg,#e8ece6 0%,#dfe7dc 45%,#e9eaee 100%)}
.col-title{position:absolute;font-size:26px;font-weight:600;color:var(--ink)}
.col-text{position:absolute;font-size:13.5px;line-height:28px;color:var(--text)}
.field-label{position:absolute;left:100px;font-size:13px;color:var(--text)}
.field{position:absolute;left:100px;width:467px;height:39px;border:1px solid var(--line);background:var(--white)}
/* footer */
.site-footer{position:absolute;left:0;top:4712px;width:1200px;height:69px;background:var(--navy);color:var(--white)}
.copyright{position:absolute;left:100px;top:24px;font-size:14px}
.social{position:absolute;right:100px;top:22px;display:flex;gap:16px;font-size:13px}
</style>
</head>
<body>

<header class="site-header">
  <div class="brand"><span class="brand-square"></span><span class="brand-name">Bramble Acres</span></div>
  <nav class="nav">
    <a style="left:596px">HOME</a>
    <a style="left:687px">ABOUT</a>
    <a style="left:784px">SERVICES</a>
    <a style="left:900px">PROJECTS</a>
    <a style="left:1024px">CONTACT</a>
  </nav>
</header>

<section class="hero" role="img" aria-label="City skyline at sunset with trees in the foreground"></section>
<h1 class="hero-title">Building the<br>future together</h1>
<p class="hero-text">Lorem ipsum dolor sit amet, consectetur cing elit sd do eiusmod tempor incididunt</p>
<a class="btn" style="left:100px;top:451px;width:148px;height:35px">Get started</a>

<h2 class="section-title" style="top:768px"><b>Our</b> Services</h2>
<div class="title-rule" style="top:824px"></div>

<article class="service-card" style="left:100px">
  <div class="service-photo" role="img" aria-label="Business team meeting at a laptop" style="background:linear-gradient(135deg,#cfd6dc,#8e9aa4 60%,#5b5650)"></div>
  <h3>Investment Focus</h3>
  <p>Lorem ipsum dolor sit amet, consectetur adipiscing elit, sed do eiusor incididunt ut labore et dolore magna aliqua.</p>
  <a class="text-link">Learn more</a>
</article>
<article class="service-card" style="left:441px">
  <div class="service-photo" role="img" aria-label="Construction site with cranes at sunset" style="background:linear-gradient(180deg,#d9b887,#a47a4e 55%,#4d3b2c)"></div>
  <h3>Development</h3>
  <p>Lorem ipsum dolor sit amet, consectetur adipiscing elit, sed do eiusor incididunt ut labore et dolore magna aliqua.</p>
  <a class="text-link">Learn more</a>
</article>
<article class="service-card" style="left:783px">
  <div class="service-photo" role="img" aria-label="Hands reviewing building plans with a hard hat" style="background:linear-gradient(135deg,#f1f1ef,#d6d3cb 55%,#b89a62)"></div>
  <h3>Preconstruction Planning</h3>
  <p>Lorem ipsum dolor sit amet, consectetur adipiscing elit, sed do eiusor incididunt ut labore et dolore magna aliqua.</p>
  <a class="text-link">Learn more</a>
</article>

<div class="about-panel"></div>
<div class="about-photo" role="img" aria-label="Three team members standing outdoors in front of city buildings"></div>
<h2 class="about-title"><b>About</b> Us</h2>
<p class="about-text">Lorem ipsum dolor sit amet, consectetur adipcing el sed do eiusmod tempordunt ut labore &nbsp;dolore magna aliqua. Quis ipsum suspendises gravida. Risus commodo viverra maecenas accs vel facilisis. Lorem ipsum dolor sit amet, consectetur adipiscing d do eiusmod tempor incididunt ut labore et dolormagna aliqua. Quis ipsum suspendisse ultrices gravida. Risus commodo</p>
<a class="btn" style="left:100px;top:1760px;width:148px;height:38px">Learn more</a>

<section class="stats">
  <div class="stat" style="left:97px"><strong>2022</strong><span>Year Established</span></div>
  <div class="stat-divider" style="left:336px"></div>
  <div class="stat" style="left:349px"><strong>206</strong><span>Projects Completed</span></div>
  <div class="stat-divider" style="left:603px"></div>
  <div class="stat" style="left:629px"><strong>870</strong><span>Contractors Appointed</span></div>
  <div class="stat-divider" style="left:896px"></div>
  <div class="stat" style="left:878px"><strong>26</strong><span>Awards Won</span></div>
</section>

<h2 class="section-title" style="top:2163px"><b>Latest</b> Projects</h2>
<div class="title-rule" style="top:2219px"></div>

<div class="project" style="left:100px;top:2258px;background:linear-gradient(180deg,#8fb4d6,#c9b79c 45%,#5cb6d4 75%,#3a9cc4)" role="img" aria-label="Apartment complex with pool and lounge chairs"></div>
<div class="project" style="left:440px;top:2258px;background:linear-gradient(180deg,#5d7ea8,#2f4c72)" role="img" aria-label="Glass office building">
  <div class="project-overlay"><h4>Finibus Bonorum et</h4><p>Lorem ipsum dolor sit amet, consectetur adipiscing elit, sed do eiusmod tempor incididunt ut labore</p></div>
</div>
<div class="project" style="left:779px;top:2258px;background:linear-gradient(180deg,#51627f,#2b2f38 55%,#6c6a58)" role="img" aria-label="Modern house with lit walkway at dusk"></div>
<div class="project" style="left:100px;top:2597px;background:linear-gradient(180deg,#1d4f9e,#3a6bbd 45%,#8b6a4f 75%,#56503f)" role="img" aria-label="Hotel building entrance at twilight"></div>
<div class="project" style="left:440px;top:2597px;background:linear-gradient(180deg,#7fa8d6,#e8e8e6 40%,#c9c3b6 75%,#6b7451)" role="img" aria-label="White residential tower"></div>
<div class="project" style="left:779px;top:2597px;background:linear-gradient(180deg,#c8d4df,#8a8c8f 40%,#b9b2a6 75%,#8c8a86)" role="img" aria-label="Modern brick townhouse with red doors"></div>

<section class="clients">
  <h2 class="section-title" style="top:75px"><b>Our</b> Clients</h2>
  <div class="title-rule" style="top:131px"></div>
  <div class="client-strip"></div>
  <div class="client" style="left:189px">Norvik</div>
  <div class="client" style="left:352px">Altessa</div>
  <div class="client" style="left:519px">Quenby</div>
  <div class="client" style="left:681px">Marlowe</div>
  <div class="client" style="left:844px">Tarrow &amp; Co</div>
</section>

<h2 class="section-title" style="top:3396px"><b>Contact</b> Us</h2>
<div class="title-rule" style="top:3452px"></div>
<div class="map" role="img" aria-label="Street map of the downtown area with the office location pinned"></div>

<h3 class="col-title" style="left:100px;top:3968px">Inquiries</h3>
<p class="col-text" style="left:100px;top:4011px;width:480px">For any inquiries, questions or commendations, please call:<br>(555) 301-2277 or fill out the following form</p>
<h3 class="col-title" style="left:100px;top:4100px">Contact Us</h3>

<label class="field-label" style="top:4150px">First Name</label><div class="field" style="top:4174px"></div>
<label class="field-label" style="top:4228px">Last Name</label><div class="field" style="top:4250px"></div>
<label class="field-label" style="top:4304px">Email*</label><div class="field" style="top:4326px"></div>
<label class="field-label" style="top:4382px">Subject</label><div class="field" style="top:4404px"></div>
<label class="field-label" style="top:4458px">Message</label><div class="field" style="top:4480px;height:106px"></div>
<a class="btn" style="left:419px;top:4600px;width:148px;height:38px">Submit</a>

<h3 class="col-title" style="left:651px;top:3968px">Headquarters</h3>
<p class="col-text" style="left:651px;top:4011px">418 Larkspur Ave. 7th Floor<br>Fairmont, Texas 75019</p>
<p class="col-text" style="left:651px;top:4093px">info@brambleacres.com<br>Tel: (555) 301-2277</p>
<h3 class="col-title" style="left:651px;top:4185px">Employment</h3>
<p class="col-text" style="left:651px;top:4228px;width:420px">To apply for a job with Bramble Acres, please send a cover letter together with your C.V. to:<br>info@brambleacres.com</p>

<footer class="site-footer">
  <p class="copyright">©Copyright ©2022 Okenta Holdings. All Rights Reserved.</p>
  <div class="social"><span>Pelo</span><span>Strand</span><span>Orbi</span><span>Quill</span></div>
</footer>

</body>
</html>
```